Oil and Gas Exploration and Production company needs a business card design

We need a business card design using our logo and colors in the logo. We want a mainstream design.

```html
<!DOCTYPE html>
<html lang="en">
<head>
<meta charset="utf-8">
<title>Aurel Oil &amp; Gas – Business Card</title>
<link href="https://fonts.googleapis.com/css2?family=Work+Sans:wght@400;500;700&display=swap" rel="stylesheet">
<style>
  :root {
    --gold: #c99a33;
    --gold-pale: #f4ead6;
    --ink: #141414;
    --paper: #ffffff;
    --backdrop: #2a2a2a;
  }
  * { box-sizing: border-box; margin: 0; padding: 0; }
  html, body { width: 1200px; height: 930px; overflow: hidden; }
  body {
    background: var(--backdrop);
    font-family: "Work Sans", Arial, sans-serif;
    position: relative;
  }
  .card {
    position: absolute;
    width: 560px;
    height: 320px;
    border-radius: 16px;
    overflow: hidden;
    box-shadow: 0 10px 30px rgba(0,0,0,.45);
  }
  .card-front { left: 70px; top: 110px; background: var(--gold); }
  .card-back  { left: 570px; top: 500px; background: var(--paper); }

  .brand { display: flex; align-items: center; gap: 12px; }
  .brand-dot { width: 34px; height: 34px; border-radius: 50%; flex: none; }
  .brand-name { font-weight: 700; line-height: 1; }
  .brand-name .line-main { display: block; font-size: 64px; letter-spacing: -1px; }
  .brand-name .line-sub { display: block; font-size: 20px; letter-spacing: 6px; margin-top: 4px; }

  .card-front .brand {
    position: absolute; left: 50%; top: 50%;
    transform: translate(-50%, -50%);
    color: var(--paper);
  }
  .card-front .brand-dot { background: var(--paper); }

  .card-back .brand { position: absolute; left: 38px; top: 70px; color: var(--ink); }
  .card-back .brand-dot { background: var(--ink); width: 28px; height: 28px; }
  .card-back .brand-name .line-main { font-size: 50px; }
  .card-back .brand-name .line-sub { font-size: 16px; letter-spacing: 5px; }

  .deco-circle {
    position: absolute; right: 120px; top: -40px;
    width: 130px; height: 130px; border-radius: 50%;
    background: var(--gold-pale);
  }
  .person { position: absolute; right: 36px; top: 86px; text-align: right; }
  .person-name { color: var(--gold); font-size: 26px; font-weight: 500; }
  .person-title { color: var(--ink); font-size: 12px; letter-spacing: 1px; margin-top: 2px; }
  .rule-top {
    position: absolute; right: 36px; top: 136px;
    width: 300px; height: 2px; background: var(--gold);
  }
  .address {
    position: absolute; right: 36px; top: 156px; text-align: right;
    font-size: 13px; line-height: 1.45; color: var(--ink);
  }
  .rule-bottom {
    position: absolute; left: 38px; top: 222px;
    width: 300px; height: 2px; background: var(--gold);
  }
  .contacts { position: absolute; left: 38px; top: 236px; list-style: none; }
  .contacts li {
    display: flex; align-items: center; gap: 8px;
    font-size: 14px; color: var(--ink); line-height: 24px;
  }
  .contacts svg { width: 12px; height: 12px; fill: none; stroke: var(--gold); stroke-width: 2; }
  .contacts .accent { color: var(--gold); }
</style>
</head>
<body>
  <section class="card card-front" aria-label="Card front">
    <div class="brand">
      <span class="brand-dot"></span>
      <span class="brand-name">
        <span class="line-main">Aurel</span>
        <span class="line-sub">OIL &amp; GAS</span>
      </span>
    </div>
  </section>

  <section class="card card-back" aria-label="Card back">
    <div class="deco-circle"></div>
    <div class="brand">
      <span class="brand-dot"></span>
      <span class="brand-name">
        <span class="line-main">Aurel</span>
        <span class="line-sub">OIL &amp; GAS</span>
      </span>
    </div>

    <div class="person">
      <div class="person-name">Dale Whitmore</div>
      <div class="person-title">CFO</div>
    </div>
    <div class="rule-top"></div>
    <address class="address" style="font-style:normal">
      2450 Meridian Ave,<br>Cedar Falls, Texas US
    </address>

    <div class="rule-bottom"></div>
    <ul class="contacts">
      <li>
        <svg viewBox="0 0 12 12"><path d="M2 1h2l1 3-1.5 1a6 6 0 0 0 3.5 3.5L8 7l3 1v2a1 1 0 0 1-1 1A9 9 0 0 1 1 2a1 1 0 0 1 1-1z"/></svg>
        (555) 014-2290
      </li>
      <li>
        <svg viewBox="0 0 12 12"><rect x="1" y="2.5" width="10" height="7"/><path d="M1 2.5l5 4 5-4"/></svg>
        info@aureloilgas.com
      </li>
      <li>
        <svg viewBox="0 0 12 12"><circle cx="6" cy="6" r="5"/><path d="M1 6h10M6 1c2 2.5 2 7.5 0 10M6 1c-2 2.5-2 7.5 0 10"/></svg>
        <span>www.<span class="accent">aureloilgas</span>.com</span>
      </li>
    </ul>
  </section>
</body>
</html>
```